Velmora Consulting Business

** Please add the content information from my old business card
1. I would like to see a two sided business card with both options with the 1st Option--Tallow Spire-new WHITE BACKGROUND LOGO
2 nd Option-Tallow Spire - new BLACK- Background Logo
3rd -Option a business card with my Photo on the card
Please add the new word to the card information:
EXECUTION
AS THE OWNER'S REP
WE AIM TO ACHIEVE YOUR
INFRASTRUCTURE VISION with
OUR SPECIALIZATION & EXECUTION in:

FUNDING Planning
BUSINESS Planning
INFRASTRUCTURE Planning
PROJECT Management
Since 2012
_____________________________________________________________________
I want to get spot uv raised printing. I was liking a a nice rich white linen paper stock with black writing & NOT A COLORED CARD other than a variety of white or black cards concept

```html
<!DOCTYPE html>
<html lang="en">
<head>
<meta charset="utf-8">
<title>Velmora Consulting – Business Cards</title>
<link href="https://fonts.googleapis.com/css2?family=Montserrat:wght@400;500;700;800&display=swap" rel="stylesheet">
<style>
  :root{
    --stage:#2b2b2b;
    --ink:#111111;
    --paper:#ffffff;
    --red:#e3193b;
    --muted:#d8d8d8;
  }
  *{box-sizing:border-box;margin:0;padding:0}
  html,body{width:1200px;height:900px;overflow:hidden;background:var(--stage);font-family:"Montserrat",sans-serif}
  .canvas{position:relative;width:1200px;height:900px}
  .card{position:absolute;width:740px;height:420px;border-radius:18px;overflow:hidden}

  /* back side */
  .card--back{left:90px;top:30px;background:var(--ink);color:var(--paper)}
  .brand{position:absolute;display:flex;align-items:center;gap:12px}
  .brand__mark{width:18px;height:18px;background:currentColor}
  .brand__name{font-weight:800;line-height:1}
  .brand__name span{display:block;font-size:.32em;letter-spacing:.55em;margin-top:8px}
  .card--back .brand{left:70px;top:165px;color:var(--paper)}
  .card--back .brand__name{font-size:54px}
  .divider{position:absolute;left:360px;top:95px;width:3px;height:230px;background:var(--red)}
  .pitch{position:absolute;left:395px;top:95px;color:var(--red);font-weight:800;font-size:14.5px;line-height:1.35;text-transform:uppercase}
  .services{position:absolute;left:395px;top:205px;list-style:none;font-size:16px;line-height:1.65}
  .services li{display:flex;align-items:center;gap:12px}
  .services li::before{content:"";width:9px;height:9px;background:var(--red);flex:none}
  .since{position:absolute;right:40px;bottom:36px;font-size:14px}

  /* front side */
  .card--front{left:370px;top:455px;background:var(--paper);color:var(--ink)}
  .card--front .brand{left:40px;top:70px;color:var(--ink)}
  .card--front .brand__name{font-size:60px}
  .locations{position:absolute;left:45px;top:205px;font-size:15px;font-weight:500}
  .contacts{position:absolute;left:45px;top:250px;list-style:none;font-size:15px;line-height:1.9}
  .contacts li{display:flex;align-items:center;gap:12px}
  .contacts svg{width:16px;height:16px;flex:none}
  .portrait{position:absolute;left:470px;top:20px;width:250px;height:300px;border-radius:10px;
    background:radial-gradient(circle at 50% 28%,#c98a5a 0 22%,transparent 23%),linear-gradient(180deg,#f3f3f3 0%,#f3f3f3 45%,#1b1b1b 46%,#111 100%)}
  .band{position:absolute;left:0;top:0;width:740px;height:420px}
  .person{position:absolute;right:28px;top:338px;text-align:right}
  .person__name{color:var(--red);font-weight:800;font-size:24px}
  .person__title{color:var(--paper);font-size:14px;letter-spacing:.04em;margin-top:4px}
</style>
</head>
<body>
<main class="canvas">

  <section class="card card--back" aria-label="Card back">
    <div class="brand">
      <span class="brand__mark"></span>
      <div class="brand__name">Velmora<span>CONSULTING</span></div>
    </div>
    <div class="divider"></div>
    <p class="pitch">As the owner's rep<br>we aim to achieve your<br>infrastructure vision with<br>our specialization in:</p>
    <ul class="services">
      <li>FUNDING Planning</li>
      <li>BUSINESS Planning</li>
      <li>INFRASTRUCTURE Planning</li>
      <li>PROJECT Management</li>
    </ul>
    <p class="since">Since 2012</p>
  </section>

  <section class="card card--front" aria-label="Card front">
    <div class="portrait" role="img" aria-label="Portrait photo of the CEO in a black top, arms crossed"></div>
    <svg class="band" viewBox="0 0 740 420" aria-hidden="true">
      <polygon points="0,396 430,396 470,326 740,326 740,420 0,420" fill="#111"/>
      <polygon points="0,392 428,392 425,398 0,398" fill="#e3193b"/>
      <rect x="0" y="398" width="430" height="22" fill="#fff"/>
    </svg>
    <div class="brand">
      <span class="brand__mark"></span>
      <div class="brand__name">Velmora<span>CONSULTING</span></div>
    </div>
    <p class="locations">Northvale NT · Harrowgate NB</p>
    <ul class="contacts">
      <li><svg viewBox="0 0 16 16"><path d="M4 1l3 3-2 2c1 2 3 4 5 5l2-2 3 3-2 3C7 15 1 9 1 3z" fill="#e3193b"/></svg>867.555.0193</li>
      <li><svg viewBox="0 0 16 16"><rect x="1" y="3" width="14" height="10" fill="#e3193b"/><path d="M1 3l7 6 7-6" stroke="#fff" stroke-width="1.4" fill="none"/></svg>renata@velmora.ca</li>
      <li><svg viewBox="0 0 16 16"><circle cx="8" cy="8" r="7" fill="#e3193b"/><path d="M1 8h14M8 1c-3 4-3 10 0 14M8 1c3 4 3 10 0 14" stroke="#fff" stroke-width="1.1" fill="none"/></svg>www.velmora.ca</li>
    </ul>
    <div class="person">
      <p class="person__name">Renata Holloway-Marsh</p>
      <p class="person__title">CEO / LEAD PROJECT MANAGER</p>
    </div>
  </section>

</main>
</body>
</html>
```